first fantastic look and impression

We are looking for a concept for letterhead, business card, emailfooter and template for invoices or offers for our company in the consultation business.
The dancer is a symbol who we are: it looks simple, but there is a lot of hard work and many years of training in this movement. The look is also what we want: elegant, modern, strong, with a touch of extravaganza
Target Market(s)
Hotelbusiness , Consulting
Font styles to use
Sans Serif
Other font styles liked:
- please give us a option we are open
Requirements
Must have
- We are not typical consultants but sparring partners and coaches for the hotel and that should also be expressed in the design. Maybe there is an icon that supports the whole thing. We are more modern and bolder than our industry colleagues.
we are modern, fresh, agile, fast
Nice to have
- a icon

```html
<!DOCTYPE html>
<html lang="en">
<head>
<meta charset="utf-8">
<title>Valdoran+Partner – Business Card</title>
<link href="https://fonts.googleapis.com/css2?family=Raleway:wght@500;700&family=Roboto:wght@400&display=swap" rel="stylesheet">
<style>
  :root {
    --backdrop: #959595;
    --card-light: #f7f7f6;
    --card-dark: #141414;
    --ink: #1d2030;
    --ink-soft: #6e6e72;
    --rule: #9a9a9a;
    --silver: #c9c9cc;
    --edge-gold: #a8893e;
  }
  * { box-sizing: border-box; margin: 0; padding: 0; }
  html, body {
    width: 1200px; height: 1020px; overflow: hidden;
    background: var(--backdrop);
  }
  .sheet {
    position: relative; width: 1200px; height: 1020px;
  }
  .card {
    position: absolute; left: 180px; width: 840px; height: 480px;
    border-bottom: 3px solid var(--edge-gold);
  }
  .card--front { top: 20px; background: var(--card-light); color: var(--ink); }
  .card--back { top: 520px; background: var(--card-dark); }

  .brand {
    position: absolute; top: 70px; right: 60px;
    display: flex; align-items: center; gap: 14px;
    font-family: "Raleway", sans-serif; font-weight: 700;
    font-size: 30px; letter-spacing: 4px; text-transform: uppercase;
    color: var(--ink);
  }
  .brand__square { width: 18px; height: 18px; background: currentColor; }

  .holder { position: absolute; left: 60px; top: 150px; }
  .holder__name {
    font-family: "Raleway", sans-serif; font-weight: 700; font-size: 31px;
    color: var(--ink);
  }
  .holder__role {
    font-family: "Raleway", sans-serif; font-weight: 500; font-size: 21px;
    color: var(--ink-soft); margin-top: 2px;
  }
  .divider {
    position: absolute; left: 300px; right: 50px; top: 238px;
    height: 1px; background: var(--rule);
  }

  .contact {
    position: absolute; left: 60px; top: 262px; list-style: none;
    font-family: "Roboto", sans-serif; font-size: 24px; color: var(--ink-soft);
  }
  .contact__item { display: flex; align-items: center; gap: 14px; height: 38px; }
  .contact__icon { width: 22px; height: 22px; fill: none; stroke: var(--ink); stroke-width: 1.8; }
  .contact__icon--solid { fill: var(--ink); stroke: none; }

  .address {
    position: absolute; right: 50px; bottom: 40px; text-align: right;
    font-family: "Roboto", sans-serif; font-size: 24px; line-height: 1.3;
    color: var(--ink-soft); font-style: normal;
  }
  .address__company {
    font-family: "Raleway", sans-serif; font-weight: 500; font-size: 25px;
    color: var(--ink);
  }

  .back-brand {
    position: absolute; inset: 0;
    display: flex; align-items: center; justify-content: center; gap: 22px;
    font-family: "Raleway", sans-serif; font-weight: 700;
    font-size: 46px; letter-spacing: 7px; text-transform: uppercase;
    color: var(--silver);
  }
  .back-brand__square { width: 28px; height: 28px; background: currentColor; }
</style>
</head>
<body>
<main class="sheet">

  <section class="card card--front" aria-label="Business card front">
    <div class="brand"><span class="brand__square"></span>Valdoran+Partner</div>

    <div class="holder">
      <p class="holder__name">Lindenau/Austria</p>
      <p class="holder__role">Managing Director</p>
    </div>

    <div class="divider"></div>

    <ul class="contact">
      <li class="contact__item">
        <svg class="contact__icon contact__icon--solid" viewBox="0 0 24 24" aria-hidden="true">
          <path d="M6.6 2.5l3 3.2-1.7 2.6c1.2 2.6 3.2 4.7 5.8 5.9l2.6-1.7 3.2 3-1.6 3.5C11 19 5 13 3.5 4.1z"/>
        </svg>
        +56912345678
      </li>
      <li class="contact__item">
        <svg class="contact__icon contact__icon--solid" viewBox="0 0 24 24" aria-hidden="true">
          <path d="M2 5h20v14H2z"/>
          <path d="M2.8 5.8l9.2 7 9.2-7" stroke="#f7f7f6" stroke-width="1.5" fill="none"/>
        </svg>
        info@valdoranpartner.com
      </li>
      <li class="contact__item">
        <svg class="contact__icon" viewBox="0 0 24 24" aria-hidden="true">
          <circle cx="12" cy="12" r="9.5"/>
          <ellipse cx="12" cy="12" rx="4" ry="9.5"/>
          <path d="M2.5 12h19M4 7h16M4 17h16"/>
        </svg>
        www.valdoranpartner.com
      </li>
    </ul>

    <address class="address">
      <span class="address__company">Valdoran+Partner</span><br>
      48 Maple Crest Lane,<br>
      Oakridge Hill, ON L0X 1A1
    </address>
  </section>

  <section class="card card--back" aria-label="Business card back">
    <div class="back-brand"><span class="back-brand__square"></span>Valdoran+Partner</div>
  </section>

</main>
</body>
</html>
```